tinyTally Resource Book - 10 maths tasks to do outside

I need a 22 (11 pages back to back) page A6 sized book produced to standard for submission to professional printer. Needs to be as .pdf file showing guide lines and allowances for colour bleed. I have text already written and submitted as attachment in a Word file with margins set to A6 size. The theme of the materials is "Nature Play" so using lots of pictures from nature (Australia preferably) and showing lots of patterns in nature (rocks, leaves, flower petals etc). Some of the tasks refer to specific activities, such as "shadows" and "floating" so would be great to illustrate appropriately. The big emphasis is on learning outside the classroom, getting kids to engage actively with nature. I would like to see the pages as full colour - so not white background. The book itself will be spiral bound along the top edge so a margin of at least 1cm will be required at the top of each page (or the bottom of even numbered pages). Book will be printed on plastic laminated matte paper for outdoor use. Font size needs to be big enough to read. Fonts sizes, alignments and page numbers are all different at the moment and need to be standardised. One photo is included in a page as a sample if you can use it, otherwise disregard. Logo for Wattlebrook Numeracy Guild is also included to have as part of the acknowledgements at the back of the book.

Target Market(s)

Book is for early childhood and preschool teachers.

Industry/Entity Type

Education

Font styles to use
Sans Serif

Requirements
Must have
• Colour and appeal.
Nice to have
• Use of natural colours instead of bright catchy colours but that is your call.
Should not have
• American spelling

```html
<!DOCTYPE html>
<html lang="en-AU">
<head>
<meta charset="utf-8">
<title>tinyTally – Maths In Nature Inquiries – page spreads</title>
<link rel="stylesheet" href="https://fonts.googleapis.com/css2?family=Oswald:wght@400;500;600&family=PT+Sans:ital,wght@0,400;0,700;1,400&family=Tinos&family=Great+Vibes&display=swap">
<style>
:root{
  --paper:#ffffff;
  --ink:#3b3b3b;
  --eylf-blue:#3f68ab;
  --leaf-title:#6e9c3a;
  --leaf-panel:rgba(226,238,212,.93);
  --dusk-title:#6e3b78;
  --dusk-panel:rgba(236,226,236,.92);
  --ember-title:#8c3d1f;
  --ember-panel:rgba(244,232,222,.93);
  --thanks-red:#c8262c;
  --cover-brand:#5a3a8c;
  --cover-green:#4f8a2e;
  --banner-green:#6aa83a;
}
*{box-sizing:border-box;margin:0;padding:0}
html,body{width:1200px;height:765px;overflow:hidden;background:var(--paper)}
body{position:relative;font-family:"PT Sans",sans-serif;color:var(--ink)}

.page{position:absolute;width:252px;height:354px;overflow:hidden}
.row-top{top:15px}.row-bottom{top:397px}
.col-1{left:44px}.col-2{left:331px}.col-3{left:619px}.col-4{left:905px}

.scene{position:absolute;inset:0}
.scene-coast{background:
  radial-gradient(ellipse 70% 40% at 30% 55%,rgba(92,150,70,.9),transparent 70%),
  radial-gradient(ellipse 60% 35% at 80% 75%,rgba(60,130,120,.8),transparent 70%),
  linear-gradient(180deg,#5b8fc8 0%,#a6cde6 18%,#6aa25c 42%,#3f8c7a 66%,#78b6cc 100%)}
.scene-dusk{background:
  radial-gradient(ellipse 80% 25% at 50% 58%,rgba(240,170,140,.8),transparent 75%),
  linear-gradient(180deg,#54467a 0%,#8a6292 30%,#c98a98 52%,#8a6a92 72%,#463e6a 100%)}
.scene-sunset{background:
  radial-gradient(ellipse 70% 30% at 50% 55%,rgba(250,180,60,.85),transparent 75%),
  linear-gradient(180deg,#7a2c12 0%,#b84c1c 28%,#e08a2c 52%,#b8521c 74%,#4a200e 100%)}
.scene-cracked{background:radial-gradient(ellipse at 50% 35%,#f2f2f2 0%,#d6d6d6 55%,#9a9a9a 100%)}
.scene-cover{background:
  radial-gradient(ellipse 45% 35% at 20% 55%,rgba(110,150,60,.55),transparent 75%),
  radial-gradient(ellipse 40% 30% at 75% 55%,rgba(240,160,70,.45),transparent 75%),
  radial-gradient(ellipse 45% 30% at 80% 8%,rgba(190,140,200,.5),transparent 75%),
  radial-gradient(ellipse 40% 30% at 85% 88%,rgba(200,120,190,.45),transparent 75%),
  linear-gradient(180deg,#f6f4ee 0%,#f1f0ea 100%)}

.panel{position:absolute;left:20px;top:22px;width:212px;height:300px;padding:9px 10px}
.theme-leaf .panel{background:var(--leaf-panel)}
.theme-dusk .panel{background:var(--dusk-panel)}
.theme-ember .panel{background:var(--ember-panel)}

.task-title{font-family:"Oswald",sans-serif;font-weight:500;font-size:16px;line-height:1.1;padding-bottom:4px;border-bottom:1px solid currentColor;margin-bottom:6px}
.theme-leaf .task-title{color:var(--leaf-title)}
.theme-dusk .task-title{color:var(--dusk-title)}
.theme-ember .task-title{color:var(--ember-title)}

.outcome{font-weight:700;font-size:8.6px;color:var(--eylf-blue);line-height:1.22;margin-bottom:5px}
.lead{font-style:italic;font-size:8.2px;line-height:1.25;margin-top:4px}
.body{font-size:8.2px;line-height:1.25}
.body > p:not(.lead):not(.label){padding-left:8px}
.body ul{list-style:none;margin:1px 0 2px 6px}
.body li{position:relative;padding-left:9px}
.body li::before{content:"";position:absolute;left:0;top:4px;width:3.4px;height:3.4px;border-radius:50%;background:var(--ink)}
.label{font-weight:700;font-size:8.6px;margin-top:5px}
.theme-leaf .label{color:var(--leaf-title)}
.theme-dusk .label{color:var(--dusk-title)}
.theme-ember .label{color:var(--ember-title)}

.folio{position:absolute;left:18px;width:216px;bottom:5px;height:14px;background:var(--paper);display:flex;align-items:center;gap:10px;padding:0 8px;font-family:"Oswald",sans-serif;font-size:7px;letter-spacing:.5px;text-transform:uppercase}
.folio.right{justify-content:flex-end}
.folio .num{font-size:7.6px;font-weight:600}
.theme-leaf .folio{color:var(--leaf-title)}
.theme-dusk .folio{color:var(--dusk-title)}
.theme-ember .folio{color:var(--ember-title)}

.art{position:absolute}
.art-leaves{right:48px;bottom:56px;width:74px;height:74px;border-radius:50%;border:3px solid #6aa040;background:rgba(110,156,58,.12)}
.art-rocks{left:44px;width:166px;bottom:44px;height:40px;border-radius:16px;background:linear-gradient(90deg,#8f8b80 0%,#bba98a 45%,#d9773a 100%)}
.art-stones{left:68px;width:122px;bottom:54px;height:28px;border-radius:10px;background:linear-gradient(90deg,#5c5854,#6d6862,#5a5550)}

/* cover */
.cover-brand{position:absolute;left:26px;top:38px}
.cover-brand .name{font-family:"Oswald",sans-serif;font-weight:600;font-size:28px;line-height:1;color:var(--cover-brand)}
.cover-brand .sub{font-family:"Oswald",sans-serif;font-weight:500;font-size:14px;color:var(--cover-green);margin-top:4px}
.cover-banner{position:absolute;left:21px;right:0;top:293px;padding:8px 10px;background:var(--banner-green);color:#fff;font-weight:700;font-size:8.4px;line-height:1.3}

/* thanks */
.thanks-card{position:absolute;left:20px;top:20px;width:216px;height:326px;border-radius:12px;background:linear-gradient(180deg,#cfe0f2 0%,rgba(255,255,255,.95) 20%,rgba(255,255,255,.95) 100%);padding:12px 13px;font-family:"Tinos",serif;font-size:8.4px;line-height:1.27;color:#222}
.thanks-title{font-family:"Great Vibes",cursive;font-weight:400;font-size:28px;color:var(--thanks-red);text-align:center;line-height:1;border-bottom:1px solid var(--thanks-red);padding-bottom:2px;margin:0 4px 9px}
.thanks-card p{margin-bottom:6px}
.quote{font-family:"Tinos",serif;font-size:22px;line-height:0;color:var(--thanks-red);font-weight:700;vertical-align:-8px}
</style>
</head>
<body>

<section class="page row-top col-1">
  <div class="scene scene-cover" role="img" aria-label="Photograph of a paper colour wheel with leaves, flowers and petals on a white table"></div>
  <div class="cover-brand">
    <div class="name">tinyTally</div>
    <div class="sub">Maths In Nature Inquiries</div>
  </div>
  <div class="cover-banner">Sponsored by the Riverbend Council Nature Play Grants Program and the Wattlebrook Numeracy Guild</div>
</section>

<section class="page row-top col-2">
  <div class="scene scene-cracked" role="img" aria-label="Photograph of cracked dry earth"></div>
  <div class="thanks-card">
    <h2 class="thanks-title">Thanks</h2>
    <p><span class="quote">“</span> I would like to acknowledge the Wirramba people, the tradition custodians of the land and cares for the magnificent environment in which Wattlebrook is located and through which we are engaging in this project.</p>
    <p>I would like to acknowledge the support of the Riverbend Council Nature Play Grant Program and the Wattlebrook Numeracy Guild in the production of this resource.</p>
    <p>I would also like to thank the following people who contributed to the ideas and development of the resource:</p>
    <p>Nadia Corbin, Rochelle Fenwick, Emmeline Grant, Alec Holloway, Jodie Langford, Tessa Lowry, Margo Quinlan, Julia Renshaw, Marion Radley, Leigh Whitford, Anya Welling, Sally Winton</p>
    <p>Original artwork by Paul Tremayne, Blue Heron Images. <span class="quote">”</span></p>
  </div>
</section>

<section class="page row-top col-3 theme-leaf">
  <div class="scene scene-coast" role="img" aria-label="Photograph of green coastal cliffs and blue sea"></div>
  <div class="panel">
    <h2 class="task-title">1. HOW MANY LEAVES?</h2>
    <p class="outcome">EYLF – Outcome 1: Children have a strong sense of identity</p>
    <div class="body">
      <p class="lead">Children learn to interact in relation to others with care, empathy and respect when they…</p>
      <p>display awareness of and respect for others’ perspectives</p>
      <p class="lead">Educators promote this learning when they…</p>
      <p>organise learning environments in ways that promote small group interactions and play experiences</p>
      <p class="lead">This task provides an opportunity to:</p>
      <ul>
        <li>explore the concepts of “perspective” and “comparing”</li>
        <li>attempt the same task in different ways</li>
        <li>consider relationship between the individual and the group</li>
      </ul>
    </div>
  </div>
  <div class="folio"><span class="num">2</span><span>tinyTally: Maths In Nature Inquiries</span></div>
</section>

<section class="page row-top col-4 theme-leaf">
  <div class="scene scene-coast" role="img" aria-label="Photograph of green coastal cliffs and blue sea"></div>
  <div class="panel">
    <h2 class="task-title">1. HOW MANY LEAVES?</h2>
    <div class="body">
      <ul>
        <li>Get a collection of leaves</li>
        <li>Draw a 20cm x 20cm square (approx.) on the ground</li>
        <li>Find how many of the leaves it takes to cover the square</li>
      </ul>
      <p class="label">Prompting questions</p>
      <ul><li>Will it be the same if I change the way I arrange the leaves? Try several different arrangements.</li></ul>
      <p class="label">Variations</p>
      <ul>
        <li>Change the types of leaves used</li>
        <li>Change the size of the box</li>
        <li>Use bodies to measure big spaces</li>
      </ul>
      <p class="label">Big Ideas</p>
      <ul><li>Area</li><li>Measure</li><li>Count</li><li>Space</li></ul>
    </div>
  </div>
  <div class="art art-leaves" role="img" aria-label="Round badge illustration of green leaves"></div>
  <div class="folio right"><span>tinyTally: Maths In Nature Inquiries</span><span class="num">3</span></div>
</section>

<section class="page row-bottom col-1 theme-dusk">
  <div class="scene scene-dusk" role="img" aria-label="Photograph of a lake at dusk with pink and purple sky"></div>
  <div class="panel">
    <h2 class="task-title">2. BIG BIGGER BIGGEST</h2>
    <p class="outcome">EYLF – Outcome 2: Children are connected with and contribute to their world</p>
    <div class="body">
      <p class="lead">Children become socially responsible and show respect for the environment when they…</p>
      <p>explore relationships with other living and non-living things and observe, notice and respond to change</p>
      <p class="lead">Educators promote this learning when they…</p>
      <p>provide children with access to a range of natural materials in their environment</p>
      <p class="lead">This task provides an opportunity to:</p>
      <ul>
        <li>explore the concepts of “change” and “growth”</li>
        <li>discuss how growth happens</li>
        <li>make predictions about change</li>
        <li>formulate strategies for coping with change.</li>
      </ul>
    </div>
  </div>
  <div class="folio"><span class="num">4</span><span>tinyTally: Maths In Nature Inquiries</span></div>
</section>

<section class="page row-bottom col-2 theme-dusk">
  <div class="scene scene-dusk" role="img" aria-label="Photograph of a lake at dusk with pink and purple sky"></div>
  <div class="panel">
    <h2 class="task-title">2. BIG BIGGER BIGGEST</h2>
    <div class="body">
      <ul>
        <li>Find an object – stone, leaf, stick etc</li>
        <li>Now find a bigger one</li>
        <li>Now find an even bigger one than that</li>
        <li>Line them up – big bigger biggest</li>
        <li>Keep adding to your line</li>
      </ul>
      <p class="label">Prompting questions</p>
      <ul>
        <li>Where do you put new rocks in the line?</li>
        <li>Can you take away some rocks to make your “biggest” the “smallest”?</li>
      </ul>
      <p class="label">Variations</p>
      <ul><li>Small Smaller Smallest</li><li>Long Longer Longest</li></ul>
      <p class="label">Big Ideas</p>
      <ul><li>Comparison</li><li>Visualization</li><li>Prediction</li></ul>
    </div>
  </div>
  <div class="art art-rocks" role="img" aria-label="Illustration of three rocks growing in size"></div>
  <div class="folio right"><span>tinyTally: Maths In Nature Inquiries</span><span class="num">5</span></div>
</section>

<section class="page row-bottom col-3 theme-ember">
  <div class="scene scene-sunset" role="img" aria-label="Photograph of an orange outback sunset"></div>
  <div class="panel">
    <h2 class="task-title">3. SAME SAME DIFFERENT</h2>
    <p class="outcome">EYLF – Outcome 2: Children are connected with and contribute to their world</p>
    <div class="body">
      <p class="lead">Children respond to diversity with respect when they…</p>
      <p>notice and react in positive ways to similarities and differences among people</p>
      <p class="lead">Educators promote this learning when they…</p>
      <p>plan experiences and provide resources that broaden children’s perspectives and encourage appreciation of diversity</p>
      <p class="lead">This task provides an opportunity to:</p>
      <ul>
        <li>explore the concepts of “same” and “different”</li>
        <li>discuss diversity</li>
        <li>model and sort based on specific criteria</li>
        <li>celebrate similarities and differences</li>
      </ul>
    </div>
  </div>
  <div class="folio"><span class="num">6</span><span>tinyTally: Maths In Nature Inquiries</span></div>
</section>

<section class="page row-bottom col-4 theme-ember">
  <div class="scene scene-sunset" role="img" aria-label="Photograph of an orange outback sunset with kangaroo silhouettes"></div>
  <div class="panel">
    <h2 class="task-title">3. SAME SAME DIFFERENT</h2>
    <div class="body">
      <ul>
        <li>Get 3 objects</li>
        <li>Ask partner to say which two are the same and which one is different</li>
        <li>Discuss attributes that are the same and different</li>
        <li>Swap roles with partner</li>
      </ul>
      <p class="label">Prompting questions</p>
      <ul><li>Can you keep the same objects but have a new “different” object?</li></ul>
      <p class="label">Variations</p>
      <ul><li>Same Same Same</li><li>Different Different Different</li></ul>
      <p class="label">Big Ideas</p>
      <ul><li>Same and different</li><li>Justifying an idea</li><li>Finding relationships</li><li>Compare and contrast</li></ul>
    </div>
  </div>
  <div class="art art-stones" role="img" aria-label="Illustration of three grey stones"></div>
  <div class="folio right"><span>tinyTally: Maths In Nature Inquiries</span><span class="num">7</span></div>
</section>

</body>
</html>
```